Surgical Device Brochure for New surgical wound care product (Veltrina)

Four page brochure for surgical device (8.5 x 11). The purpose of this flyer is convince hospital adminstrators and surgeons that Veltrina will save hospitals millions of dollars each year while saving lives and improving patient care.

Use the provided text in the attached document which has the main points. the last page should be space for people to take notes and perform their own calculations. On page 3, please highlight the questions we ask which will help them figure out how much money our product will save them. page 1 and 2 should cover the main points in the document, have quotes, and interesting graphics and layout.

Target Market(s)

Hospital Administrators and Surgeons (medical doctors) and financial controllers

Industry/Entity Type

Medical

Font styles to use
Serif

Colors
85abd2
b7a5cd
fbee3e
e667a6

Requirements
Must have
• Four pages, last page has caption at top with space for notes.
• Emphasis on hospital cost control
Nice to have
• Nice graphics of surgeons, surgery centers, emergency rooms, and surgical tools and graphs showing profits going up and costs going down
• dynamic, exciting, high-tech, clean, organized.
Should not have
• too much red. text that is too small.

```html
<!DOCTYPE html>
<html lang="en">
<head>
<meta charset="utf-8">
<title>Veltrina Brochure Cover</title>
<link href="https://fonts.googleapis.com/css2?family=Montserrat:wght@500&family=Open+Sans:wght@400;700&display=swap" rel="stylesheet">
<style>
  :root {
    --backdrop: #e4e4e4;
    --paper: #ffffff;
    --teal: #1a9d93;
    --teal-deep: #138a81;
    --scrub: #1f8f86;
    --theatre-light: #c9d8dc;
    --text-light: #ffffff;
  }
  * { margin: 0; padding: 0; box-sizing: border-box; }
  html, body {
    width: 1200px; height: 1000px; overflow: hidden;
    background: var(--backdrop);
    font-family: "Open Sans", Arial, sans-serif;
  }
  .cover {
    position: absolute; left: 250px; top: 47px;
    width: 700px; height: 906px;
    background: var(--paper);
    box-shadow: 0 6px 24px rgba(0,0,0,0.12);
  }
  .brand {
    position: absolute; top: 82px; left: 0; width: 100%;
    text-align: center; color: var(--teal);
  }
  .brand-name {
    font-family: "Montserrat", Arial, sans-serif; font-weight: 500;
    font-size: 40px; letter-spacing: 3px; text-transform: uppercase;
  }
  .brand-tagline {
    font-family: "Montserrat", Arial, sans-serif; font-weight: 500;
    font-size: 11px; letter-spacing: 0.5px; margin-top: 2px;
  }
  .accent-bar {
    position: absolute; left: 110px; top: 186px;
    width: 520px; height: 12px; background: var(--teal);
  }
  .hero-photo {
    position: absolute; left: 70px; top: 198px;
    width: 560px; height: 300px;
    background: linear-gradient(135deg, var(--theatre-light) 0%, #7fb8b3 40%, var(--scrub) 75%, #1b6f6a 100%);
  }
  .inset-photo {
    position: absolute;
    border: 2px solid var(--paper);
  }
  .inset-tools { left: 495px; top: 408px; width: 135px; height: 90px;
    background: linear-gradient(135deg, #dfe9f0, #7ea9c9); }
  .inset-team { left: 355px; top: 432px; width: 140px; height: 66px;
    background: linear-gradient(135deg, #3d7fa8, #1d5e86); }
  .inset-instruments { left: 70px; top: 450px; width: 110px; height: 48px;
    background: linear-gradient(135deg, #f2f2f2, #9aa3a8); }
  .facts-panel {
    position: absolute; left: 70px; top: 498px;
    width: 560px; height: 290px;
    background: var(--teal);
    color: var(--text-light);
    padding: 26px 28px;
    font-size: 12.5px; line-height: 1.42;
  }
  .facts-panel p + p { margin-top: 12px; }
  .facts-panel strong { font-weight: 700; }
  .site-url {
    position: absolute; left: 0; width: 100%; top: 838px;
    text-align: center; color: var(--teal); font-size: 11px;
  }
</style>
</head>
<body>
  <main class="cover">
    <header class="brand">
      <div class="brand-name">Veltrina</div>
      <div class="brand-tagline">Close with Veltrina</div>
    </header>

    <div class="accent-bar"></div>
    <div class="hero-photo" role="img" aria-label="Surgical team in green scrubs operating in a theatre"></div>
    <div class="inset-photo inset-instruments" role="img" aria-label="Surgical instruments on a tray"></div>
    <div class="inset-photo inset-team" role="img" aria-label="Operating room with surgeons under blue light"></div>
    <div class="inset-photo inset-tools" role="img" aria-label="Gloved hand holding a wound closure device"></div>

    <section class="facts-panel">
      <p>In 2016, the Federal Government increased CivicCare penalties to $528 million, which currently impacts 2,597 hospitals with an average amount of $203,000 per facility. (Dana Whitfield, August 4, 2016, Harbor Health Report, civicnews.org)</p>
      <p>Surgical Site Infection costs hospitals between <strong>$11,000</strong> to <strong>$35,000</strong> for each case of infection.</p>
      <p>Ridgeland Dept. of Health "Surgical Site Infection (SSI) continues to represent a significant portion of healthcare associated infections." - National Council on Health Services.</p>
      <p>Hospitals that reduce their Surgical Site Infection rate stand to <strong>save</strong> an estimated <strong>$1</strong> to <strong>$2 million per year</strong> annual SSI Related Cost savings. - Ridgeland Dept. of Health</p>
    </section>

    <footer class="site-url">www.closewithveltrina.com</footer>
  </main>
</body>
</html>
```